Powerpoint and Word template required

We need PowerPoint and Word templates for all of our company branded materials and stationary. We have recently rebranded our website and would like something that is reflective of our new corporate branding. A sample of some of the documents we have created recently are attached and our website is below

http://lorwynmedical.com.au/

The word template will be used for all letters we send to clients and customers and we think we want the logo and ISO 9001 cert to only appear on the first page.

The powerpoint template has to be flexible as we use this for both marketing and training purposes. I have attached a couple of samples of the types of documents we create and note that these are very basic / crude and we would be looking for something that is a significant improvement on these

In the powerpoint template it would be good to have lots of standard layouts within the template, e.g. different 'standard layouts for multiple elements on a page including pictures and text etc.
Updates

Project Deadline Extended
Reason: Still looking for a professional yet modern template and important to us that we can see more tan just a title slide and the layout of the other slide master slides is very important to us. Many thanks, Dale

Industry/Entity Type

Healthcare

Font styles to use
Sans Serif

Colors
33a6d7

Requirements
Must have
• Templates must be versatile for use; powerpoint template must be able to be used for training materials and weel as marketing / pitch books.
• Word template must be able to be used as a basis for our corporate letter head through to RFP response type documents as well as Reference / Operating manual type of documents
• In terms of the design it must be consistent with our new corporate image which is best represented by our new website design; www.lorwynmedical.com

```html
<!DOCTYPE html>
<html lang="en">
<head>
<meta charset="utf-8">
<title>Lorwyn Medical – Slide Templates</title>
<link rel="stylesheet" href="https://fonts.googleapis.com/css2?family=Open+Sans:wght@400;600;700&display=swap">
<style>
:root{
  --backdrop:#6b6566;
  --paper:#ffffff;
  --brand:#2a80c5;
  --ink:#1e1e1e;
  --muted:#6a6a6a;
  --photo-light:#e3f1f7;
  --photo-mid:#a9cfe0;
  --photo-deep:#6fa6c4;
}
*{margin:0;padding:0;box-sizing:border-box}
html,body{width:1003px;height:1200px;overflow:hidden}
body{background:var(--backdrop);font-family:"Open Sans",Arial,sans-serif;color:var(--ink);position:relative}
.slide{position:absolute;background:var(--paper);overflow:hidden}
.slide-heading{position:absolute;left:42px;top:22px;font-size:13.5px;font-weight:700;color:var(--brand)}
.slide-subtitle{position:absolute;left:42px;top:42px;font-size:10px;font-weight:700;color:var(--muted)}
.brand{position:absolute;right:20px;top:14px;display:flex;align-items:center;gap:4px;font-size:15px;font-weight:600;color:var(--brand)}
.brand-square{width:14px;height:14px;background:var(--brand)}
.footer-url{position:absolute;left:14px;bottom:20px;font-size:6px;font-weight:700;color:#444}
.lead{font-size:9.4px;font-weight:700;line-height:1.12;margin-bottom:9px}
.body-copy{font-size:5.6px;font-weight:700;line-height:1.45}
.body-copy p{margin-bottom:7px}
.block{position:absolute}
.subheading{font-size:13px;font-weight:700;color:var(--brand);margin:6px 0 5px}
.photo-portrait{position:absolute;background:radial-gradient(circle at 70% 30%,#f4f1ee 0 18%,transparent 40%),linear-gradient(135deg,var(--photo-light),var(--photo-mid) 55%,var(--photo-deep))}
.photo-banner{position:absolute;background:linear-gradient(90deg,#cfe2ee 0%,#eef5fa 22%,var(--photo-mid) 50%,#e2eef6 78%,#f3f8fb 100%)}
.two-col{column-count:2;column-gap:10px}
</style>
</head>
<body>

<!-- Slide: text with portrait, two sections -->
<section class="slide" style="left:42px;top:27px;width:453px;height:351px">
  <h1 class="slide-heading">Insert your Heading Here</h1>
  <h2 class="slide-subtitle">Sub Title Here</h2>
  <div class="brand"><span class="brand-square"></span>Lorwyn</div>
  <div class="block" style="left:42px;top:72px;width:225px">
    <p class="lead">Lorwyn Healthcare is the leading supplier of high quality, clinically proven products for the prevention and management of pressure ulcers in the acute, community and residential care sectors.</p>
    <div class="body-copy">
      <p>Our clinically proven products are supported by a portfolio of quality assured services such as 24/7 rental service, expert training and education, equipment management solutions as well as service and maintenance programs.<br>Lorwyn Healthcare guarantees a first class level of service that will enable you to provide the world's best practice in pressure area care</p>
    </div>
    <h3 class="subheading">Insert your SubHeading Here</h3>
    <div class="body-copy">
      <p>Our clinically proven products are supported by a portfolio of quality assured services such as 24/7 rental service, expert training and education, equipment management solutions as well as service and maintenance programs.</p>
      <p>Lorwyn Healthcare guarantees a first class level of service that will enable you to provide the world's best practice in pressure area care<br>Lorwyn Healthcare is the leading supplier of high quality, clinically proven products for the prevention and management of pressure ulcers in the</p>
    </div>
  </div>
  <div class="photo-portrait" role="img" aria-label="Photo of a doctor touching floating health icons" style="left:281px;top:72px;width:125px;height:124px"></div>
  <div class="block body-copy" style="left:281px;top:204px;width:125px">ssured services such as 24/7 rental service, expert training and education, equipment management solutions as well as service and maintenance programs.</div>
  <p class="footer-url">www.lorwynmedical.com</p>
</section>

<!-- Slide: portrait left, text right, full-width copy -->
<section class="slide" style="left:522px;top:27px;width:451px;height:349px">
  <h1 class="slide-heading">Insert your Heading Here</h1>
  <h2 class="slide-subtitle">Sub Title Here</h2>
  <div class="brand"><span class="brand-square"></span>Lorwyn</div>
  <div class="photo-portrait" role="img" aria-label="Photo of a doctor touching floating health icons" style="left:42px;top:72px;width:129px;height:131px"></div>
  <div class="block" style="left:183px;top:72px;width:225px">
    <p class="lead">Lorwyn Healthcare is the leading supplier of high quality, clinically proven products for the prevention and management of pressure ulcers in the acute, community and residential care sectors.</p>
    <div class="body-copy">
      <p>Our clinically proven products are supported by a portfolio of quality assured services such as 24/7 rental service, expert training and education, equipment management solutions as well as service and maintenance programs.</p>
      <p>Lorwyn Healthcare guarantees a first class level of service that will enable you to provide the world's best practice in pressure area care<br>Lorwyn Healthcare is the leading supplier of high quality, clinically proven products for the prevention and management of pressure ulcers in the acute, community and residential care sectors.</p>
    </div>
  </div>
  <div class="block body-copy" style="left:42px;top:213px;width:370px">
    <p>Our clinically proven products are supported by a portfolio of quality assured services such as 24/7 rental service, expert training and education, equipment management solutions as well as service and maintenance programs.</p>
    <p>Lorwyn Healthcare guarantees a first class level of service that will enable you to provide the world's best practice in pressure area care Lorwyn Healthcare is the leading supplier of high quality, clinically proven products for the prevention and</p>
  </div>
  <p class="footer-url">www.lorwynmedical.com</p>
</section>

<!-- Slide: banner with two columns -->
<section class="slide" style="left:42px;top:427px;width:448px;height:345px">
  <h1 class="slide-heading">Insert your Heading Here</h1>
  <h2 class="slide-subtitle">Sub Title Here</h2>
  <div class="brand"><span class="brand-square"></span>Lorwyn</div>
  <div class="photo-banner" role="img" aria-label="Banner photo of gloved hands with stethoscope and medical hexagon icons" style="left:45px;top:61px;width:359px;height:119px"></div>
  <p class="block lead" style="left:45px;top:189px;width:362px">Lorwyn Healthcare is the leading supplier of high quality, clinically proven products for the prevention and management of pressure ulcers in the acute, community and residential care sectors.</p>
  <div class="block body-copy two-col" style="left:45px;top:232px;width:362px;height:72px">
    <p>Lorwyn Healthcare is the leading supplier of high quality, clinically proven products for the prevention and management of pressure ulcers in the acute, community and residential care sectors.</p>
    <p>Our clinically proven products are supported by a portfolio of quality assured services such as 24/7 rental service, expert training and education, equipment management solutions as well as service and maintenance programs.</p>
    <p>Lorwyn Healthcare guarantees a first class level of service that will enable you to provide the world's best practice in pressure area care<br>Lorwyn Healthcare is the leading supplier of high quality, clinically proven products for the prevention and management of pressure ulcers in the acute, community and residential care</p>
  </div>
  <p class="footer-url">www.lorwynmedical.com</p>
</section>

<!-- Slide: portrait with single text column -->
<section class="slide" style="left:527px;top:427px;width:445px;height:343px">
  <h1 class="slide-heading">Insert your Heading Here</h1>
  <h2 class="slide-subtitle">Sub Title Here</h2>
  <div class="brand"><span class="brand-square"></span>Lorwyn</div>
  <div class="photo-portrait" role="img" aria-label="Photo of a doctor touching floating health icons" style="left:41px;top:70px;width:112px;height:125px"></div>
  <div class="block" style="left:196px;top:70px;width:205px">
    <p class="lead">Lorwyn Healthcare is the leading supplier of high quality, clinically proven products for the prevention and management of pressure ulcers in the acute, community and residential care sectors.</p>
    <div class="body-copy">
      <p>Our clinically proven products are supported by a portfolio of quality assured services such as 24/7 rental service, expert training and education, equipment management solutions as well as service and maintenance programs.</p>
      <p>Lorwyn Healthcare guarantees a first class level of service that will enable you to provide the world's best practice in pressure area care Lorwyn Healthcare is the leading supplier of high quality, clinically proven products for the prevention and management of pressure ulcers in the acute, community and residential care sectors.</p>
      <p>Our clinically proven products are supported by a portfolio of quality assured services such as 24/7 rental service, expert training and education, equipment management solutions as well as service and maintenance programs.</p>
      <p>Lorwyn Healthcare guarantees a first class level of service that will enable you to provide the world's best practice in pressure area care</p>
    </div>
  </div>
  <p class="footer-url">www.lorwynmedical.com</p>
</section>

<!-- Slide: banner with two columns (variant) -->
<section class="slide" style="left:42px;top:808px;width:447px;height:345px">
  <h1 class="slide-heading">Insert your Heading Here</h1>
  <h2 class="slide-subtitle">Sub Title Here</h2>
  <div class="brand"><span class="brand-square"></span>Lorwyn</div>
  <div class="photo-banner" role="img" aria-label="Banner photo of gloved hands with stethoscope and medical hexagon icons" style="left:45px;top:61px;width:359px;height:118px"></div>
  <p class="block lead" style="left:45px;top:188px;width:362px">Lorwyn Healthcare is the leading supplier of high quality, clinically proven products for the prevention and management of pressure ulcers in the acute, community and residential care sectors.</p>
  <div class="block body-copy two-col" style="left:45px;top:232px;width:362px;height:72px">
    <p>Lorwyn Healthcare is the leading supplier of high quality, clinically proven products for the prevention and management of pressure ulcers in the acute, community and residential care sectors.</p>
    <p>Our clinically proven products are supported by a portfolio of quality assured services such as 24/7 rental service, expert training and education, equipment management solutions as well as service and maintenance programs.</p>
    <p>Lorwyn Healthcare guarantees a first class level of service that will enable you to provide the world's best practice in pressure area care<br>Lorwyn Healthcare is the leading supplier of high quality, clinically proven products for the prevention and management of pressure ulcers in the acute, community and residential care</p>
  </div>
  <p class="footer-url">www.lorwynmedical.com</p>
</section>

</body>
</html>
```